Bramblewood Joinery Website

My client Bramblewood Joinery is looking for a redesign for a Word Press Website. Their current site is at www.bramblewoodjoinery.example They are a custom cabinet company, but also create bathroom, living room, bar and entertainment and bedroom cabinets too. They would like a design that emulates the master craftsman work they do yet a contemporary style.

Their current site was designed using Flash elements.

Target Market(s)

Home owners and builders of high end homes

Industry/Entity Type

Entertainment

Font styles to use
Serif
Decorative

Requirements
Must have
• Must show their work and logo using a contemporary style.
Nice to have
• Sliders that showcase their projects.

```html
<!DOCTYPE html>
<html lang="en">
<head>
<meta charset="utf-8">
<title>Bramblewood Joinery</title>
<link href="https://fonts.googleapis.com/css2?family=Open+Sans:wght@400;600;700&display=swap" rel="stylesheet">
<style>
:root{
  --green:#3aaa35;
  --green-text:#3d9b37;
  --ink:#333333;
  --body:#555555;
  --muted:#777777;
  --line:#dddddd;
  --band:#f5f5f5;
  --footer:#3a3a3a;
  --dark:#222222;
  --white:#ffffff;
}
*{box-sizing:border-box;margin:0;padding:0}
html,body{width:742px;height:1200px;overflow:hidden}
body{position:relative;background:var(--white);font-family:"Open Sans",Arial,sans-serif;color:var(--body)}
.abs{position:absolute}
.top-rule{left:0;top:0;width:742px;height:2px;background:var(--green)}
.brand{left:37px;top:22px;display:flex;align-items:center;gap:6px}
.brand-dot{width:14px;height:14px;border-radius:50%;background:var(--green)}
.brand-name{font-size:12px;font-weight:700;color:var(--green-text)}
.nav{top:35px;left:0;width:742px;height:12px;font-size:8.4px;color:#666}
.nav span{position:absolute;white-space:nowrap}
.nav .active{color:var(--green)}
.hero{left:36px;top:79px;width:670px;height:344px;border:1px solid var(--line);
  background:linear-gradient(90deg,#6a86a8 0%,#8fb0d0 30%,#a9c3d8 45%,#8a7b68 62%,#7b6e5e 100%)}
.hero-floor{position:absolute;left:0;bottom:0;width:100%;height:30%;background:linear-gradient(#c8a679,#dcc09a)}
.hero-shadow{left:100px;top:423px;width:540px;height:14px;background:radial-gradient(ellipse at top,rgba(0,0,0,.18),rgba(0,0,0,0) 70%)}
.dots{display:flex;gap:3px}
.dots i{display:block;width:6px;height:6px;border-radius:50%;border:1px solid #555;background:transparent}
.dots i.on{background:#555}
.hero-dots{left:359px;top:403px}
.video{left:67px;top:448px;width:217px;height:134px;border:2px solid #bbb;background:linear-gradient(135deg,#3a2e27,#7a6656 50%,#b8ab98)}
.video-bar{position:absolute;left:0;bottom:0;width:100%;height:11px;background:#111;display:flex;align-items:center;gap:6px;padding-left:6px;font-size:5px;color:#ddd}
.h2{font-size:11.2px;font-weight:600;color:var(--green-text);letter-spacing:.2px;text-transform:uppercase}
.about-title{left:311px;top:446px}
.about-text{left:311px;top:464px;width:350px;font-size:8.5px;line-height:14.4px;color:var(--body)}
.btn-outline{left:311px;top:562px;width:73px;height:20px;border:1px solid #cfe6cd;font-size:7.5px;font-weight:600;color:var(--green-text);display:flex;align-items:center;justify-content:center}
.offer-title{left:38px;top:624px}
.card{width:200px;top:650px}
.card-img{width:200px;height:102px;border:2px solid #eee}
.card-title{margin-top:14px;padding-left:6px;font-size:8.4px;font-weight:600;color:var(--ink)}
.card-text{margin-top:6px;padding:0 12px 0 7px;font-size:8px;line-height:13.2px;text-align:justify;color:var(--muted)}
.card-foot{position:relative;height:24px;border-bottom:1px solid #999}
.card-foot svg{position:absolute;right:2px;top:4px}
.band{left:0;top:860px;width:742px;height:175px;background:var(--band)}
.testi-title{left:74px;top:877px}
.testi-box{left:73px;top:902px;width:287px;height:111px;border:1px solid var(--line);background:var(--band)}
.quote{position:absolute;left:11px;top:6px;font-size:20px;font-weight:700;color:#666;line-height:1}
.testi-text{position:absolute;left:23px;top:21px;width:254px;font-size:7.2px;line-height:10.4px;color:var(--ink)}
.avatar{position:absolute;left:22px;top:73px;width:34px;height:34px;border-radius:50%;background:linear-gradient(#c9c2bb,#8a8580)}
.testi-name{position:absolute;left:74px;top:74px;font-size:9.6px;color:var(--green-text)}
.testi-role{position:absolute;left:74px;top:90px;font-size:7.2px;color:var(--ink)}
.testi-dots{position:absolute;left:225px;top:88px}
.testi-dots i{border-color:#333;width:6px;height:6px}
.testi-dots i.on{background:var(--green);border-color:var(--green)}
.news-title{left:395px;top:877px}
.news-item{left:397px;width:290px;height:52px}
.news-img{position:absolute;left:0;top:0;width:77px;height:52px}
.news-head{position:absolute;left:95px;top:0;font-size:8.4px;color:var(--green-text)}
.news-text{position:absolute;left:95px;top:13px;width:190px;font-size:8px;line-height:11px;color:var(--ink)}
.news-time{position:absolute;left:95px;top:41px;font-size:7px;color:var(--green-text)}
.sub-band{left:0;top:1035px;width:742px;height:109px;background:var(--green)}
.sub-text{left:0;top:1056px;width:742px;text-align:center;font-size:11.2px;font-weight:600;color:var(--white)}
.sub-form{left:173px;top:1096px;width:396px;height:24px;display:flex}
.sub-input{flex:1;border:1px solid #2a7d27;display:flex;align-items:center;gap:7px;padding-left:11px;font-size:7.6px;color:#cde9cb}
.sub-btn{width:83px;background:var(--dark);color:var(--white);font-size:9px;font-weight:600;display:flex;align-items:center;justify-content:center}
.footer{left:0;top:1144px;width:742px;height:56px;background:var(--footer)}
.social{left:331px;top:1157px;display:flex;gap:3px}
.social i{display:block;width:14px;height:14px;border-radius:3px;background:var(--white)}
.copy{left:0;top:1179px;width:742px;text-align:center;font-size:7.2px;font-weight:600;color:var(--white)}
</style>
</head>
<body>
<div class="abs top-rule"></div>

<header>
  <div class="abs brand"><span class="brand-dot"></span><span class="brand-name">Bramblewood Joinery</span></div>
  <nav class="abs nav">
    <span class="active" style="left:200px">Home</span>
    <span style="left:239px">Who We Are</span>
    <span style="left:302px">Getting Started</span>
    <span style="left:375px">Contact Us</span>
    <span style="left:432px">Customer Experience</span>
    <span style="left:526px">Professional</span>
    <span style="left:589px">Portfolio</span>
    <span style="left:637px">Cabinet Hardware</span>
  </nav>
</header>

<section>
  <div class="abs hero" role="img" aria-label="Modern living room with white armchairs and a sea view through tall windows"><div class="hero-floor"></div></div>
  <div class="abs hero-shadow"></div>
  <div class="abs dots hero-dots"><i class="on"></i><i></i><i></i></div>
</section>

<section>
  <div class="abs video" role="img" aria-label="Video still of a finished custom kitchen with cabinetry">
    <div class="video-bar"><span>&#9654;</span><span>0:00</span></div>
  </div>
  <h2 class="abs h2 about-title">Who We Are</h2>
  <p class="abs about-text">Consequuntur magni dolores eos qui ratione voluptatem sequi nesciunt. Neque porro quisquam est, qui dolorem ipsum quia dolor sit amet, consectetur, adipisci velit, sed quia non numquam eius modi tempora incidunt ut labore et dolore magnam aliquam quaerat voluptatem. Ut enim ad minima veniam, quis nostrum exercitationem ullam corporis suscipit laboriosam, nisi ut aliquid ex ea commodi consequatur&nbsp; Quis autem vel eum iure&nbsp; qui in ea voluptate</p>
  <div class="abs btn-outline">READ MORE</div>
</section>

<section>
  <h2 class="abs h2 offer-title">What We Offer</h2>
  <article class="abs card" style="left:48px">
    <div class="card-img" role="img" aria-label="Bright kitchen with cream cabinets" style="background:linear-gradient(135deg,#6b5843,#cdbb9c 60%,#e9e2d4)"></div>
    <h3 class="card-title">KITCHENS</h3>
    <p class="card-text">Adipisci velit, sed quia non numquam eius modi tempora incidunt ut labore et dolore magnam aliquam quaerat voluptatem.</p>
    <div class="card-foot"><svg width="12" height="10" viewBox="0 0 12 10"><path d="M0 5h11M7 1l4 4-4 4" fill="none" stroke="#555" stroke-width="1"/></svg></div>
  </article>
  <article class="abs card" style="left:270px">
    <div class="card-img" role="img" aria-label="Open office interior with warm light" style="background:linear-gradient(135deg,#4a3a34,#c79a70 55%,#f1e3cf)"></div>
    <h3 class="card-title">OFFICE</h3>
    <p class="card-text">Adipisci velit, sed quia non numquam eius modi tempora incidunt ut labore et dolore magnam aliquam quaerat voluptatem.</p>
    <div class="card-foot"><svg width="12" height="10" viewBox="0 0 12 10"><path d="M0 5h11M7 1l4 4-4 4" fill="none" stroke="#555" stroke-width="1"/></svg></div>
  </article>
  <article class="abs card" style="left:492px">
    <div class="card-img" role="img" aria-label="Large empty workshop hall" style="background:linear-gradient(180deg,#8fa088,#d9ddd2 55%,#eef0ea)"></div>
    <h3 class="card-title">WORKSHOPS</h3>
    <p class="card-text">Adipisci velit, sed quia non numquam eius modi tempora incidunt ut labore et dolore magnam aliquam quaerat voluptatem.</p>
    <div class="card-foot"><svg width="12" height="10" viewBox="0 0 12 10"><path d="M0 5h11M7 1l4 4-4 4" fill="none" stroke="#555" stroke-width="1"/></svg></div>
  </article>
</section>

<section>
  <div class="abs band"></div>
  <h2 class="abs h2 testi-title">Testimonials</h2>
  <div class="abs testi-box">
    <div class="quote">&ldquo;</div>
    <p class="testi-text">Numquam eius modi tempora labore dolore magnamUt enim inimam, ullam corporis suscipit laboriosam,voluptatem accusantium doloremque laudantium, totam rem aperiam, eaque ipsa quae ab illo inventore</p>
    <div class="avatar" role="img" aria-label="Client portrait"></div>
    <div class="testi-name">Corwen</div>
    <div class="testi-role">lorem ipsum</div>
    <div class="dots testi-dots"><i class="on"></i><i></i><i></i></div>
  </div>

  <h2 class="abs h2 news-title">Latest News</h2>
  <div class="abs news-item" style="top:903px">
    <div class="news-img" role="img" aria-label="Kitchen island with white cabinets" style="background:linear-gradient(135deg,#2e2a27,#9a8f82 60%,#d8d2c8)"></div>
    <div class="news-head">IPSUM DOLOR</div>
    <p class="news-text">sed quia non numquam eius modi tempora incidunt ut labore et dolore</p>
    <div class="news-time">1 day ago</div>
  </div>
  <div class="abs news-item" style="top:963px">
    <div class="news-img" role="img" aria-label="Dark wood cabinetry" style="background:linear-gradient(135deg,#1f1915,#4a3a30 60%,#8b7a6a)"></div>
    <div class="news-head">IPSUM DOLOR</div>
    <p class="news-text">sed quia non numquam eius modi tempora incidunt ut labore et dolore</p>
    <div class="news-time">1 day ago</div>
  </div>
</section>

<section>
  <div class="abs sub-band"></div>
  <p class="abs sub-text">Subscribe to our free mailing list for announcements, freebies and more!</p>
  <form class="abs sub-form">
    <div class="sub-input">
      <svg width="10" height="8" viewBox="0 0 10 8"><rect x=".5" y=".5" width="9" height="7" fill="none" stroke="#cde9cb"/><path d="M.5 .5l4.5 4 4.5-4" fill="none" stroke="#cde9cb"/></svg>
      <span>Enter your mail address and start receiving the interiors</span>
    </div>
    <div class="sub-btn">SUBSCRIBE</div>
  </form>
</section>

<footer>
  <div class="abs footer"></div>
  <div class="abs social"><i></i><i></i><i></i><i></i><i></i></div>
  <p class="abs copy">Copyright &copy; 2015 Bramblewood Joinery. All Rights Reserved.</p>
</footer>
</body>
</html>
```